Business card for Luxury Portable Restroom Trailer company

We are a Luxury Portable Restroom Trailer Company Called FALCRIDGE HIRES. Based in Orange County California. We provide portable restroom trailers for events, such as, Weddings, Concerts, Charity events, Sporting events, Tournaments, Corporate events, ect. We rent and Sell the Luxury restrooms. Our colors are white, grey, and Orange. As you will see in the logo we uploaded.
There are 2 people in the company so the names and titles will change for the 3 people but card will remain the same. Here is the information for each Person: Dwight Penner CFO 555 318-0476
next Person: Leon Marchetti VP 555 318-0476
Next Person: Owen Marchetti CEO 555 318-0476
Information to include on the card: Luxury Restroom Trailers Rental and Sales. Weddings, Concerts, Charity, Sporting and Corp. Events.

```html
<!DOCTYPE html>
<html lang="en">
<head>
<meta charset="utf-8">
<title>Falcridge Hires – Business Card</title>
<link href="https://fonts.googleapis.com/css2?family=Montserrat:wght@500;600;800&display=swap" rel="stylesheet">
<style>
  :root {
    --orange: #f26b23;
    --grey: #58585a;
    --ink: #1c1c1c;
    --white: #ffffff;
    --backdrop: #d9d9d9;
  }
  * { box-sizing: border-box; margin: 0; padding: 0; }
  html, body { width: 1200px; height: 856px; overflow: hidden; }
  body {
    background: var(--backdrop);
    font-family: "Montserrat", sans-serif;
    display: flex;
    align-items: center;
    justify-content: center;
    gap: 40px;
  }
  .card {
    position: relative;
    width: 540px;
    height: 309px;
    overflow: hidden;
    box-shadow: 0 10px 24px rgba(0,0,0,.25);
  }

  /* Front side */
  .card--front { background: var(--white); }
  .front__swoosh { position: absolute; inset: 0; }
  .brand {
    position: absolute;
    top: 46px;
    left: 150px;
    color: var(--grey);
    font-weight: 800;
    font-size: 28px;
    line-height: 1.05;
    letter-spacing: 1px;
  }
  .team {
    position: absolute;
    left: 30px;
    top: 132px;
    display: flex;
    flex-direction: column;
    gap: 9px;
  }
  .person__name {
    color: var(--orange);
    font-weight: 800;
    font-size: 15px;
    letter-spacing: .5px;
    text-transform: uppercase;
  }
  .person__title,
  .person__phone {
    color: var(--ink);
    font-weight: 500;
    font-size: 11px;
    line-height: 1.35;
  }
  .person__phone { display: flex; align-items: center; gap: 6px; }
  .person__phone svg { width: 11px; height: 11px; fill: var(--orange); }

  /* Back side */
  .card--back {
    background: var(--orange);
    color: var(--white);
    display: flex;
    flex-direction: column;
    align-items: center;
    justify-content: center;
    gap: 34px;
    text-align: center;
  }
  .brand--back {
    position: static;
    color: var(--white);
    font-size: 40px;
    letter-spacing: 2px;
  }
  .services {
    font-weight: 600;
    font-size: 13px;
    line-height: 1.7;
    list-style: none;
  }
  .services li { display: inline; }
  .services li::before { content: "\25CF"; margin: 0 6px 0 8px; font-size: 10px; }
</style>
</head>
<body>

  <article class="card card--front">
    <svg class="front__swoosh" viewBox="0 0 540 309" aria-hidden="true">
      <path d="M405 0 C398 150 310 255 190 309 L540 309 L540 0 Z" fill="var(--orange)"/>
      <path d="M392 40 C385 160 300 255 170 309 L184 309 C306 255 393 160 392 40 Z" fill="var(--grey)"/>
    </svg>

    <div class="brand">FALCRIDGE<br>HIRES</div>

    <div class="team">
      <div class="person">
        <div class="person__name">Dwight Penner</div>
        <div class="person__title">CFO</div>
        <div class="person__phone">
          <svg viewBox="0 0 24 24"><path d="M6.6 10.8a15.1 15.1 0 0 0 6.6 6.6l2.2-2.2a1 1 0 0 1 1-.25 11.4 11.4 0 0 0 3.6.57 1 1 0 0 1 1 1V20a1 1 0 0 1-1 1A17 17 0 0 1 3 4a1 1 0 0 1 1-1h3.5a1 1 0 0 1 1 1c0 1.25.2 2.45.57 3.57a1 1 0 0 1-.25 1z"/></svg>
          555 318-0476
        </div>
      </div>
      <div class="person">
        <div class="person__name">Leon Marchetti</div>
        <div class="person__title">VP</div>
        <div class="person__phone">
          <svg viewBox="0 0 24 24"><path d="M6.6 10.8a15.1 15.1 0 0 0 6.6 6.6l2.2-2.2a1 1 0 0 1 1-.25 11.4 11.4 0 0 0 3.6.57 1 1 0 0 1 1 1V20a1 1 0 0 1-1 1A17 17 0 0 1 3 4a1 1 0 0 1 1-1h3.5a1 1 0 0 1 1 1c0 1.25.2 2.45.57 3.57a1 1 0 0 1-.25 1z"/></svg>
          555 318-0476
        </div>
      </div>
      <div class="person">
        <div class="person__name">Owen Marchetti</div>
        <div class="person__title">CEO</div>
        <div class="person__phone">
          <svg viewBox="0 0 24 24"><path d="M6.6 10.8a15.1 15.1 0 0 0 6.6 6.6l2.2-2.2a1 1 0 0 1 1-.25 11.4 11.4 0 0 0 3.6.57 1 1 0 0 1 1 1V20a1 1 0 0 1-1 1A17 17 0 0 1 3 4a1 1 0 0 1 1-1h3.5a1 1 0 0 1 1 1c0 1.25.2 2.45.57 3.57a1 1 0 0 1-.25 1z"/></svg>
          555 318-0476
        </div>
      </div>
    </div>
  </article>

  <article class="card card--back">
    <div class="brand brand--back">FALCRIDGE<br>HIRES</div>
    <ul class="services">
      <li>Luxury Restroom Trailers Rental and Sales</li><br>
      <li>Weddings</li><li>Concerts</li><li>Charity</li><li>Sporting and Corp</li><li>Events</li>
    </ul>
  </article>

</body>
</html>
```